Bright and beautiful business card for a coach

I'm a personal and business coach based in Perth, Australia. I need a business card that whilst subtle and elegant, will stand out and appeal on a table full of cards.

My business name is Fern Mentoring and the business card must represent the warmth and brightness implied in the name, without being gimmicky. It must have a warmth and appeal and be easy to read.

I prefer clean, minimalist designs.

It must align with the feel of my website and socials: https://www.fernmentoring-example.com.au/
https://www.instagram.com/fernmentoringau/
https://www.facebook.com/fernmentoringau
Updates

Hi Designers Thank you so much for taking the time to submit designs. I wonder if I could have explained myself a little better. Most of the designs that have been submitted look rather formal and many have quite corporate looking embellishments on them (to my eye). I would like softer, warmer, more organic. I’m open to people playing about and being more abstract, using softer embellishments (e.g the line drawing flowers and grasses I’ve used in my socials) incorporating other colours from my palette or like the social icons in my email signature (in PDF), perhaps playing with size/oversize, playing with the bleed. Please don’t be constrained by what I’ve already done, it merely needs to compliment. I’m sorry if I’m not using the right words or have led you astray. I’m no designer, but I’ve done my website, socials, email signature etc all myself (my logo was a design contest) and I was really hoping for my business card to be something more creative than I could have made with a template. Reminder: No black cards/sides please. Thank you 😊

Target Market(s)

Individuals, most likely but not all female. Creative thinkers. Likely professionals.

Industry/Entity Type

Business & Personal Coach

Contact Information for Business Card

(Fern Mentoring Logo) Name: Greta Pellham; Title: Business & Personal Coach; Phone number: +61 (0)458 913307; Email: greta@fernmentoring-example.com.au; Website: https://fernmentoring-example.com.au; Social icons for Facebook, Instagram & LinkedIn: @fernmentoringAU. Optional strapline: "A thinking partner to help you cut through the noise"

Font styles to use
Sans Serif

Colors
00AB8E
00BBA5
67D7C9
C6EFE9
E9F9F6
59FF00
82FF00
B8FF75
E3FFCB
F4FFEA
FFC000
F8CF3A
FAE287
FDF2CF
FEFAEE

Requirements
Must have
• Must align with feel of my website and socials. Must have a pop of #FFC000 (possibly whole of one side, or at least a block). Bright or white background. Easy to read.
Nice to have
• Possibly incorporate the sunshine/grass picture I have used in website and socials - will upload.
Should not have
• Must not be black or dark. Not impersonal or corporate looking.

```html
<!DOCTYPE html>
<html lang="en">
<head>
<meta charset="utf-8">
<title>Fern Mentoring – Business Card</title>
<link rel="stylesheet" href="https://fonts.googleapis.com/css2?family=Allison&family=Lato:wght@400;700&display=swap">
<style>
  :root {
    --canvas: #e4e4e2;
    --card: #fefaee;
    --card-back: #ffffff;
    --sun: #ffc000;
    --sun-deep: #d89a00;
    --sun-soft: #fdf2cf;
    --ink: #2a2b2d;
    --ink-muted: #6e6f72;
    --rule: #b9b4a6;
  }
  * { box-sizing: border-box; margin: 0; padding: 0; }
  html, body {
    width: 1200px;
    height: 1108px;
    overflow: hidden;
    background: var(--canvas);
  }
  .canvas {
    position: relative;
    width: 1200px;
    height: 1108px;
  }
  .card {
    position: absolute;
    top: 198px;
    width: 460px;
    height: 712px;
    border-radius: 28px;
    background: var(--card);
    box-shadow: 0 18px 40px rgba(0,0,0,.18);
    overflow: hidden;
    color: var(--ink);
    font-family: "Lato", sans-serif;
    text-align: center;
  }
  .card--front { left: 80px; }
  .card--back { left: 660px; background: var(--card-back); }

  /* front */
  .brand-name {
    position: absolute;
    left: 0; right: 0;
    top: 160px;
    font-weight: 400;
    font-size: 44px;
    line-height: 1.1;
    letter-spacing: 4px;
    color: var(--sun-deep);
  }
  .person-name {
    position: absolute;
    left: 0; right: 0;
    top: 318px;
    font-family: "Allison", cursive;
    font-size: 80px;
    line-height: 1;
    color: var(--sun-deep);
  }
  .person-title {
    position: absolute;
    left: 0; right: 0;
    top: 394px;
    font-size: 22px;
    color: var(--ink);
  }
  .divider-row {
    position: absolute;
    left: 60px; right: 60px;
    display: flex;
    align-items: center;
    gap: 10px;
  }
  .divider-row .rule {
    flex: 1;
    height: 1px;
    background: var(--rule);
  }
  .divider-row--contact { top: 448px; }
  .divider-row--social { top: 612px; }
  .icon-tile {
    width: 34px; height: 34px;
    border-radius: 5px;
    background: var(--sun);
    display: flex; align-items: center; justify-content: center;
  }
  .icon-tile svg { width: 20px; height: 20px; }
  .social-dot {
    width: 32px; height: 32px;
    border-radius: 50%;
    background: var(--sun);
  }
  .contact-list {
    position: absolute;
    left: 0; right: 0;
    top: 500px;
    list-style: none;
    font-size: 19px;
    line-height: 30px;
    color: var(--ink);
  }
  .contact-list .accent { color: var(--sun-deep); }
  .social-handle {
    position: absolute;
    left: 0; right: 0;
    top: 656px;
    font-size: 21px;
    color: var(--ink);
  }

  /* back */
  .brand-pattern {
    position: absolute;
    inset: 0;
    background: linear-gradient(160deg, #ffffff 0%, var(--sun-soft) 60%, #fae287 100%);
  }
  .back-brand {
    position: absolute;
    left: 0; right: 0;
    top: 420px;
    font-weight: 400;
    font-size: 34px;
    letter-spacing: 3px;
    color: var(--sun-deep);
  }
  .strapline {
    position: absolute;
    left: 26px; right: 20px;
    top: 486px;
    font-family: "Allison", cursive;
    font-size: 46px;
    line-height: 1.1;
    text-align: left;
    color: var(--ink);
  }
  .strapline .line { display: block; white-space: nowrap; }
  .strapline .line--indent { padding-left: 90px; }
</style>
</head>
<body>
<main class="canvas">

  <section class="card card--front" aria-label="Card front">
    <h1 class="brand-name">Fern Mentoring</h1>
    <p class="person-name">Greta Pellham</p>
    <p class="person-title">Business &amp; Personal Coach</p>

    <div class="divider-row divider-row--contact">
      <span class="rule"></span>
      <span class="icon-tile" aria-hidden="true">
        <svg viewBox="0 0 24 24"><path fill="#2a2b2d" d="M6.6 10.8a15.1 15.1 0 0 0 6.6 6.6l2.2-2.2c.3-.3.7-.4 1-.2 1.1.4 2.3.6 3.6.6.6 0 1 .4 1 1V20c0 .6-.4 1-1 1A17 17 0 0 1 3 4c0-.6.4-1 1-1h3.5c.6 0 1 .4 1 1 0 1.3.2 2.5.6 3.6.1.3 0 .7-.2 1z"/></svg>
      </span>
      <span class="icon-tile" aria-hidden="true">
        <svg viewBox="0 0 24 24"><rect x="3" y="5" width="18" height="14" rx="1.5" fill="none" stroke="#2a2b2d" stroke-width="2"/><path d="M3.5 6l8.5 7 8.5-7M3.5 18.5l6.5-6M20.5 18.5l-6.5-6" fill="none" stroke="#2a2b2d" stroke-width="1.6"/></svg>
      </span>
      <span class="icon-tile" aria-hidden="true">
        <svg viewBox="0 0 24 24"><circle cx="12" cy="12" r="8.5" fill="none" stroke="#2a2b2d" stroke-width="2"/><path d="M3.5 12h17M12 3.5c3 3 3 14 0 17M12 3.5c-3 3-3 14 0 17" fill="none" stroke="#2a2b2d" stroke-width="1.5"/></svg>
      </span>
      <span class="rule"></span>
    </div>

    <ul class="contact-list">
      <li>+61 (0)458 913307</li>
      <li>greta@fernmentoring-example.com.au</li>
      <li>www.<span class="accent">fernmentoring-example</span>.com.au</li>
    </ul>

    <div class="divider-row divider-row--social">
      <span class="rule"></span>
      <span class="social-dot" aria-hidden="true"></span>
      <span class="social-dot" aria-hidden="true"></span>
      <span class="social-dot" aria-hidden="true"></span>
      <span class="rule"></span>
    </div>
    <p class="social-handle">@fernmentoringAU</p>
  </section>

  <section class="card card--back" aria-label="Card back">
    <div class="brand-pattern" role="img" aria-label="Soft repeating brand pattern in warm light tones"></div>
    <p class="back-brand">Fern Mentoring</p>
    <p class="strapline">
      <span class="line">A thinking partner to help you cut</span>
      <span class="line line--indent">through the noise</span>
    </p>
  </section>

</main>
</body>
</html>
```